TalkHarbor - Language Coaching Services

Sleek, innovative, trendy design for Language Coaching business.

TalkHarbor is a new UK based company that provides Language Coaching services. We offer highly personalized on-line and face to face language courses. We also impart learning techniques workshops based on the latest neuroscience research for second-language acquisition.

Target Market(s)

See attached info

Industry/Entity Type

Consulting

Contact Information for Business Card

TalkHarbor
DaniaKV@talkharbor.co.uk
TalkHarbor.co.uk
London, UK

Font styles to use
Sans Serif

```html
<!DOCTYPE html>
<html lang="en">
<head>
<meta charset="utf-8">
<title>TalkHarbor Business Card</title>
<link rel="stylesheet" href="https://fonts.googleapis.com/css2?family=Montserrat:wght@400;600&family=Lato:wght@400;700&display=swap">
<style>
  :root {
    --bg: #2a2a2c;
    --blue-light: #24a3cb;
    --blue-deep: #1a6c97;
    --blue-band: #2a95bd;
    --blue-ink: #1f7fae;
    --white: #ffffff;
    --paper: #f7f8f8;
  }
  * { margin: 0; padding: 0; box-sizing: border-box; }
  html, body { width: 1200px; height: 900px; overflow: hidden; }
  body {
    background: var(--bg);
    position: relative;
    font-family: "Lato", sans-serif;
  }
  .card {
    position: absolute;
    width: 560px;
    height: 320px;
    border-radius: 2px;
    overflow: hidden;
    box-shadow: 0 14px 30px rgba(0,0,0,.45);
  }

  /* Front side */
  .card-front {
    left: 130px; top: 100px;
    background: linear-gradient(35deg, var(--blue-light) 0%, #1f8ab7 55%, var(--blue-deep) 100%);
    color: var(--white);
  }
  .front-ring {
    position: absolute;
    left: 50%; top: 46%;
    width: 210px; height: 210px;
    transform: translate(-50%, -50%);
    border: 14px solid rgba(255,255,255,.12);
    border-radius: 50%;
  }
  .front-wordmark {
    position: absolute;
    left: 0; right: 0; top: 120px;
    text-align: center;
    font-family: "Montserrat", sans-serif;
    font-weight: 600;
    font-size: 46px;
    letter-spacing: 1px;
    text-transform: uppercase;
  }
  .front-url {
    position: absolute;
    left: 0; right: 0; bottom: 58px;
    text-align: center;
    font-size: 15px;
    letter-spacing: 5px;
  }

  /* Back side */
  .card-back {
    left: 510px; top: 470px;
    background: var(--paper);
  }
  .back-brand {
    position: absolute;
    left: 0; right: 0; top: 40px;
    display: flex; flex-direction: column; align-items: center;
    color: var(--blue-ink);
  }
  .brand-circle {
    width: 66px; height: 66px;
    border: 6px solid var(--blue-ink);
    border-radius: 50%;
    margin-bottom: 8px;
  }
  .back-wordmark {
    font-family: "Montserrat", sans-serif;
    font-weight: 600;
    font-size: 38px;
    letter-spacing: 1px;
    text-transform: uppercase;
  }
  .band-stripes {
    position: absolute;
    left: 0; right: 0; top: 176px;
    height: 10px;
    border-top: 2px solid var(--blue-band);
    border-bottom: 2px solid var(--blue-band);
  }
  .band {
    position: absolute;
    left: 0; right: 0; top: 190px; bottom: 0;
    background: var(--blue-band);
    color: var(--white);
    display: flex; align-items: center;
  }
  .person {
    flex: 1;
    text-align: right;
    padding-right: 28px;
  }
  .person-name { font-size: 17px; }
  .person-name strong { font-weight: 700; }
  .person-title { font-size: 13px; margin-top: 2px; }
  .divider {
    width: 2px; height: 80px;
    background: var(--white);
  }
  .contacts {
    flex: 1.3;
    list-style: none;
    padding-left: 26px;
    font-size: 14px;
  }
  .contacts li {
    display: flex; align-items: center;
    gap: 10px;
    margin: 6px 0;
  }
  .contact-icon {
    width: 20px; height: 20px;
    border-radius: 50%;
    background: var(--white);
    display: flex; align-items: center; justify-content: center;
  }
</style>
</head>
<body>

  <section class="card card-front">
    <div class="front-ring"></div>
    <div class="front-wordmark">TalkHarbor</div>
    <div class="front-url">www.TalkHarbor.co.uk</div>
  </section>

  <section class="card card-back">
    <div class="back-brand">
      <div class="brand-circle"></div>
      <div class="back-wordmark">TalkHarbor</div>
    </div>
    <div class="band-stripes"></div>
    <div class="band">
      <div class="person">
        <div class="person-name">Elena <strong>Marwood</strong></div>
        <div class="person-title">Chief Executive Offer</div>
      </div>
      <div class="divider"></div>
      <ul class="contacts">
        <li>
          <span class="contact-icon">
            <svg width="12" height="12" viewBox="0 0 24 24"><path fill="#2a95bd" d="M6.6 10.8a15 15 0 0 0 6.6 6.6l2.2-2.2c.3-.3.7-.4 1-.2 1.1.4 2.3.6 3.6.6.6 0 1 .4 1 1V20c0 .6-.4 1-1 1A17 17 0 0 1 3 4c0-.6.4-1 1-1h3.5c.6 0 1 .4 1 1 0 1.3.2 2.5.6 3.6.1.3 0 .7-.2 1z"/></svg>
          </span>
          020.7946.0321
        </li>
        <li>
          <span class="contact-icon">
            <svg width="12" height="12" viewBox="0 0 24 24"><path fill="#2a95bd" d="M6.6 10.8a15 15 0 0 0 6.6 6.6l2.2-2.2c.3-.3.7-.4 1-.2 1.1.4 2.3.6 3.6.6.6 0 1 .4 1 1V20c0 .6-.4 1-1 1A17 17 0 0 1 3 4c0-.6.4-1 1-1h3.5c.6 0 1 .4 1 1 0 1.3.2 2.5.6 3.6.1.3 0 .7-.2 1z"/></svg>
          </span>
          020.7946.0588
        </li>
        <li>
          <span class="contact-icon">
            <svg width="12" height="12" viewBox="0 0 24 24"><rect x="3" y="6" width="18" height="12" rx="1" fill="none" stroke="#2a95bd" stroke-width="2.4"/><path d="M3 7l9 6 9-6" fill="none" stroke="#2a95bd" stroke-width="2.4"/></svg>
          </span>
          DaniaKV@talkharbor.co.uk
        </li>
      </ul>
    </div>
  </section>

</body>
</html>
```